Website re-design and completion for www.brovimark.com

Graphically redesign and complete the existing site www.brovimark.com
This site intent is to:
a) introduce and educate about a new Technoloy to customers in a variety of different industries using traditional methods.
b) outline and promote the benefits and ROI of using the new techology
c) Sell our machines by showing customers the benefits and reasons to purchase from us over other suppliers
We do want to keep the overall concept. Like the home page with a slider. The most important thing to us is to increase the design of the slider. Next we need it standard layout with some attractive design to describe each product group. There are 3 product groups. Laser Cleaning Machines, Laser Welding Machines and Laser Cutting Machines

Target Market(s)

Mostly business to business.

Coding

Coded - Design and coding required

Font styles to use
Sans Serif
Other font styles liked:
• Calibri, Arial

Requirements
Must have
• A serious approach as we are targeting professionals, such as production managers, engineers and so forth
Should not have
• Annoying call to action stuff. Overly playful gimmicks.

```html
<!DOCTYPE html>
<html lang="en">
<head>
<meta charset="utf-8">
<title>Brovimark – Laser Cutting and Welding Equipment</title>
<link rel="stylesheet" href="https://fonts.googleapis.com/css2?family=Open+Sans:wght@400;600;700&family=Arimo:wght@400;700&display=swap">
<style>
:root{
  --red:#d8232f;
  --red-dark:#b81d2a;
  --blue:#1d8bd3;
  --ink:#1b1b1b;
  --text:#3d3d3d;
  --muted:#6f6f6f;
  --tint:#eef5f9;
  --field:#efefef;
  --card:#fbeeee;
  --footer:#232323;
  --white:#ffffff;
}
*{box-sizing:border-box;margin:0;padding:0}
html,body{width:1200px;height:4612px;overflow:hidden}
body{font-family:"Open Sans",Arial,sans-serif;color:var(--text);background:var(--white);position:relative}
section,header,footer{position:relative;width:1200px}
.abs{position:absolute}
.btn{display:inline-block;background:var(--red);color:var(--white);font:700 13px "Arimo",Arial,sans-serif;padding:11px 20px;border-radius:2px}
.heading{font:700 28px "Arimo",Arial,sans-serif;color:var(--ink)}
.heading span{color:var(--blue)}
.heading::after{content:"";display:block;width:56px;height:3px;background:var(--red);margin-top:10px}
.center{text-align:center}
.center.heading::after{margin:10px auto 0}
p.body{font-size:11.5px;line-height:21px;color:var(--text)}

/* header */
.site-header{height:75px;background:var(--white);box-shadow:0 1px 4px rgba(0,0,0,.08);z-index:2}
.brand{left:141px;top:18px;font:700 30px "Arimo",Arial,sans-serif;color:var(--red);letter-spacing:1px}
.brand small{display:block;font:400 8px "Arimo",Arial,sans-serif;color:var(--blue);letter-spacing:.4px;margin-top:-3px}
.nav{right:142px;top:24px;display:flex;align-items:center;gap:35px;font-size:13px;color:#333}
.nav .active{color:var(--red);border-bottom:2px solid var(--red);padding-bottom:3px}
.nav .btn{padding:10px 16px}

/* hero */
.hero{height:552px;background:linear-gradient(110deg,#1a1656 0%,#2c2a8a 35%,#6b3f8f 60%,#c0532a 78%,#3a2b7a 100%)}
.hero-title{left:141px;top:130px;width:440px;font:700 27px/39px "Open Sans",Arial,sans-serif;color:var(--white)}
.hero .btn{left:141px;top:378px}

/* about */
.about{height:718px}
.photo{border-radius:0}
.about .p1{left:141px;top:66px;width:366px;height:476px;background:linear-gradient(160deg,#3a3f4a,#c88a3a 55%,#2d2a2a)}
.about .p2{left:405px;top:460px;width:284px;height:167px;background:linear-gradient(135deg,#22364e,#5b7b9c 55%,#d7b37c)}
.about .p3{left:689px;top:510px;width:106px;height:110px;background:linear-gradient(180deg,#2b2b2b,#111);border-radius:8px}
.about .dot{left:637px;top:430px;width:92px;height:92px;border-radius:50%;background:#d5e9f7}
.about-copy{left:582px;top:68px;width:476px}
.about-copy p.body{margin-top:22px}
.about-copy p.body + p.body{margin-top:12px}
.about-copy .btn{margin-top:22px}

/* products */
.products{height:622px;background:var(--tint)}
.products .heading{position:absolute;left:0;right:0;top:50px}
.tabs{left:0;right:0;top:118px;display:flex;justify-content:center;gap:14px}
.tab{border:1.5px solid var(--red);font:700 12px "Arimo",Arial,sans-serif;color:var(--ink);padding:11px 18px;background:var(--white)}
.tab.on{background:var(--red);color:var(--white)}
.product-copy{left:141px;top:232px;width:500px}
.product-copy h3{font:700 22px "Arimo",Arial,sans-serif;color:var(--ink);margin-bottom:20px}
.product-copy p.body + p.body{margin-top:12px}
.product-copy .btn{margin-top:22px}
.products .pimg{left:761px;top:213px;width:297px;height:333px;background:linear-gradient(145deg,#3a2a22,#c8612a 50%,#f1b060 60%,#2a2220)}

/* why */
.why{height:483px}
.why .w1{left:141px;top:113px;width:257px;height:312px;background:linear-gradient(180deg,#2d3a5a,#7891b4 60%,#d8dfe9)}
.why .w2{left:305px;top:83px;width:217px;height:254px;background:linear-gradient(180deg,#2c1f1f,#b82a1f 45%,#f0a42a 80%,#3a1f12);outline:8px solid var(--white)}
.why .dots{left:100px;top:375px}
.why-copy{left:592px;top:113px;width:466px}
.why-copy ul{list-style:none;margin-top:22px}
.why-copy li{display:flex;gap:12px;font-size:11.5px;line-height:20px;margin-bottom:13px}
.why-copy li svg{flex:none;margin-top:3px}

/* testimonials */
.testimonials{height:602px}
.testimonials .heading{position:absolute;left:0;right:0;top:51px}
.quote-card{top:157px;width:448px;height:190px;background:var(--card);border-radius:18px;padding:52px 34px 0}
.quote-card p{font-size:11.5px;line-height:23px;color:var(--text)}
.quote-card::after{content:"";position:absolute;left:82px;bottom:-16px;border:16px solid transparent;border-bottom:0;border-top-color:var(--card)}
.quote-badge{top:-24px;left:54px;width:52px;height:48px;background:var(--red-dark);border-radius:50%;display:flex;align-items:center;justify-content:center}
.client{top:390px;display:flex;align-items:center;gap:14px}
.avatar{width:77px;height:77px;border-radius:50%;background:linear-gradient(135deg,#c9a58d,#5a4033)}
.client .stars{color:#f5a524;font-size:16px;letter-spacing:2px}
.client .name{font:700 16px "Arimo",Arial,sans-serif;color:var(--ink)}
.arrows{left:0;right:0;top:503px;display:flex;justify-content:center;gap:26px}

/* network */
.network{height:526px;background:var(--tint)}
.network .heading{position:absolute;left:0;right:0;top:50px}
.map{left:134px;top:127px;width:930px;height:367px;background:radial-gradient(ellipse at 30% 40%,#b7bfc7 0,#cfd5da 40%,transparent 70%),radial-gradient(ellipse at 72% 45%,#b7bfc7 0,#cfd5da 40%,transparent 70%);opacity:.85}
.pin-label{left:270px;top:157px;background:var(--white);padding:9px 18px;font-size:12.5px;color:var(--ink);box-shadow:0 2px 8px rgba(0,0,0,.1)}

/* contact */
.contact{height:637px}
.contact .cimg{left:141px;top:84px;width:394px;height:466px;background:linear-gradient(170deg,#6b5e55,#b06a2a 45%,#f0a14a 60%,#3a2a22)}
.contact-form{left:611px;top:104px;width:447px}
.row{display:flex;gap:14px;margin-top:14px}
.row:first-of-type{margin-top:34px}
.field{flex:1;height:42px;background:var(--field);font-size:11.5px;color:var(--muted);padding:0 14px;display:flex;align-items:center;justify-content:space-between}
.field.msg{height:132px;align-items:flex-start;padding-top:14px}
.contact-form .btn{margin-top:22px;padding:11px 32px}

/* footer */
.site-footer{height:397px;background:var(--footer);color:#ddd}
.foot-brand{left:141px;top:140px;font:700 36px "Arimo",Arial,sans-serif;color:var(--red);letter-spacing:1px}
.foot-brand small{display:block;font:700 10px "Arimo",Arial,sans-serif;color:var(--white);margin-top:2px;letter-spacing:.5px}
.col{top:60px}
.col h4{font:700 17px "Arimo",Arial,sans-serif;color:var(--white);margin-bottom:12px}
.col h4::after{content:"";display:block;width:46px;height:2px;background:var(--red);margin-top:8px}
.col li{list-style:none;font-size:11.5px;line-height:29.5px}
.col li.ic{display:flex;align-items:center;gap:10px;line-height:36px}
.foot-rule{left:141px;top:334px;width:917px;height:1px;background:#3c3c3c}
.copyright{left:141px;top:358px;font-size:10.5px;color:#ccc}
.social{right:142px;top:350px;display:flex;gap:10px}
.social span{width:26px;height:26px;border-radius:50%;background:var(--red);border:2px solid var(--white)}
</style>
</head>
<body>

<header class="site-header">
  <div class="abs brand">BROVIMARK<small>LASER CUTTING AND WELDING EQUIPMENT</small></div>
  <nav class="abs nav">
    <span class="active">Home</span><span>About Us</span><span>Products ⌄</span><span>Solutions</span><span>Industries</span><span>Services</span><span class="btn">Contact Us</span>
  </nav>
</header>

<section class="hero" role="img" aria-label="Laser cutting head throwing sparks under blue and purple light">
  <h1 class="abs hero-title">Experience The Power Of Laser Technology. Laser Technology And Photonics Present Superior Alternatives To Conventional Welding, Cleaning And Cutting Techniques.</h1>
  <span class="abs btn">Contact Us</span>
</section>

<section class="about">
  <div class="abs photo p1" role="img" aria-label="Two laser nozzles cutting metal with sparks"></div>
  <div class="abs dot"></div>
  <div class="abs photo p2" role="img" aria-label="Laser cutting a metal sheet"></div>
  <div class="abs p3" role="img" aria-label="Portable laser machine unit"></div>
  <div class="abs about-copy">
    <h2 class="heading">About <span>Us</span></h2>
    <p class="body">At Brovimark, we're dedicated to providing you with top-of-the-line equipment that you can rely on for all your manufacturing requirements. With years of expertise in the manufacturing industry, we understand the importance of laser photonics equipment and the myriad questions that may arise when integrating laser technology into your operations. That's why we're here to offer comprehensive support and guidance every step of the way.</p>
    <p class="body">Our team at Brovimark boasts extensive experience working directly within manufacturing processes, giving us unique insights into the challenges and demands of the industry. We meticulously test all our products to ensure they not only meet but exceed your expectations.</p>
    <span class="btn">Learn More</span>
  </div>
</section>

<section class="products">
  <h2 class="heading center">Our <span>Products</span></h2>
  <div class="abs tabs"><span class="tab">Laser Cleaning</span><span class="tab on">Laser Welding</span><span class="tab">Laser Cutting</span></div>
  <div class="abs product-copy">
    <h3>Laser Welding Machines</h3>
    <p class="body">With unmatched precision, laser welding is easy to learn, energy efficient, and remarkably fast compared to MIG and TIG welding. Handheld laser welding machines offer unparalleled speed, precision, and ease compared to traditional methods like MIG and TIG welding.</p>
    <p class="body">With its cutting-edge features, the RX1 is remarkably easy to learn and operate. Equipped with a user-friendly 7" LED touch screen and an intelligent operating system supporting multiple languages, this system simplifies the welding process like never before. The VANTA RX1-Series features an intuitive, easy-to-use interface, based on feedback from welders like you.</p>
    <span class="btn">Learn More</span>
  </div>
  <div class="abs pimg" role="img" aria-label="Handheld laser welding torch with sparks"></div>
</section>

<section class="why">
  <div class="abs w1" role="img" aria-label="Laser cutting head above a work table"></div>
  <div class="abs w2" role="img" aria-label="Laser beam cutting glowing metal"></div>
  <svg class="abs dots" width="40" height="80" viewBox="0 0 40 80"><g fill="#9bb8d3"><circle cx="3" cy="3" r="1.6"/><circle cx="18" cy="3" r="1.6"/><circle cx="33" cy="3" r="1.6"/><circle cx="3" cy="22" r="1.6"/><circle cx="18" cy="22" r="1.6"/><circle cx="33" cy="22" r="1.6"/><circle cx="3" cy="41" r="1.6"/><circle cx="18" cy="41" r="1.6"/><circle cx="33" cy="41" r="1.6"/><circle cx="3" cy="60" r="1.6"/><circle cx="18" cy="60" r="1.6"/><circle cx="33" cy="60" r="1.6"/></g></svg>
  <div class="abs why-copy">
    <h2 class="heading">Why Choose Our <span>Technology?</span></h2>
    <ul>
      <li><svg width="16" height="16" viewBox="0 0 16 16"><path d="M1 1 L15 8 L1 15 L4 8 Z" fill="none" stroke="var(--blue)" stroke-width="1.4"/><path d="M4 8 L15 8" stroke="var(--red)" stroke-width="1.4"/></svg>we are committed to providing you with the highest quality equipment that you can depend on for your manufacturing needs.</li>
      <li><svg width="16" height="16" viewBox="0 0 16 16"><path d="M1 1 L15 8 L1 15 L4 8 Z" fill="none" stroke="var(--blue)" stroke-width="1.4"/><path d="M4 8 L15 8" stroke="var(--red)" stroke-width="1.4"/></svg>We understand the manufacturing industry, the uses of laser photonics equipment.</li>
      <li><svg width="16" height="16" viewBox="0 0 16 16"><path d="M1 1 L15 8 L1 15 L4 8 Z" fill="none" stroke="var(--blue)" stroke-width="1.4"/><path d="M4 8 L15 8" stroke="var(--red)" stroke-width="1.4"/></svg>Brovimark has extensive experience working directly with the manufacturing process.</li>
      <li><svg width="16" height="16" viewBox="0 0 16 16"><path d="M1 1 L15 8 L1 15 L4 8 Z" fill="none" stroke="var(--blue)" stroke-width="1.4"/><path d="M4 8 L15 8" stroke="var(--red)" stroke-width="1.4"/></svg>Laser technology has made a revolutionary impact on manufacturing.</li>
      <li><svg width="16" height="16" viewBox="0 0 16 16"><path d="M1 1 L15 8 L1 15 L4 8 Z" fill="none" stroke="var(--blue)" stroke-width="1.4"/><path d="M4 8 L15 8" stroke="var(--red)" stroke-width="1.4"/></svg>Laser manufacturing is quickly becoming the new standard due to its efficiency, convenience, and precision.</li>
    </ul>
  </div>
</section>

<section class="testimonials">
  <h2 class="heading center">What Our Happy <span>Clients Say</span></h2>
  <div class="abs quote-card" style="left:141px">
    <div class="abs quote-badge"><svg width="24" height="20" viewBox="0 0 24 20"><path d="M2 18V10C2 5 4 2 9 1v3C6 5 5 7 5 9h4v9zM14 18V10c0-5 2-8 7-9v3c-3 1-4 3-4 5h4v9z" fill="#fff"/></svg></div>
    <p>This is due to their excellent service, competitive pricing and customer support. It's thoroughly refreshing to get such a personal touch. There are many variations of passages of Lorem Ipsum available, but the majority have suffered alteration in some form.</p>
  </div>
  <div class="abs quote-card" style="left:611px">
    <div class="abs quote-badge"><svg width="24" height="20" viewBox="0 0 24 20"><path d="M2 18V10C2 5 4 2 9 1v3C6 5 5 7 5 9h4v9zM14 18V10c0-5 2-8 7-9v3c-3 1-4 3-4 5h4v9z" fill="#fff"/></svg></div>
    <p>This is due to their excellent service, competitive pricing and customer support. It's thoroughly refreshing to get such a personal touch. There are many variations of passages of Lorem Ipsum available, but the majority have suffered alteration in some form.</p>
  </div>
  <div class="abs client" style="left:204px"><div class="avatar" role="img" aria-label="Client portrait"></div><div><div class="stars">★★★★★</div><div class="name">Nora Whitfield</div></div></div>
  <div class="abs client" style="left:673px"><div class="avatar" role="img" aria-label="Client portrait"></div><div><div class="stars">★★★★★</div><div class="name">Daniel Okafor</div></div></div>
  <div class="abs arrows">
    <svg width="30" height="14" viewBox="0 0 30 14"><path d="M29 7H2M8 1L2 7l6 6" fill="none" stroke="var(--blue)" stroke-width="2"/></svg>
    <svg width="30" height="14" viewBox="0 0 30 14"><path d="M1 7h27M22 1l6 6-6 6" fill="none" stroke="var(--blue)" stroke-width="2"/></svg>
  </div>
</section>

<section class="network">
  <h2 class="heading center">Our Global <span>Network</span></h2>
  <div class="abs map" role="img" aria-label="Dotted world map with office locations"></div>
  <div class="abs pin-label">Westfield, IL 60000</div>
  <svg class="abs" style="left:0;top:0" width="1200" height="526" viewBox="0 0 1200 526">
    <g fill="var(--red)" stroke="#fff" stroke-width="2">
      <path d="M339 223c-7 0-12 5-12 12 0 8 12 20 12 20s12-12 12-20c0-7-5-12-12-12z"/>
      <path d="M445 328c-7 0-12 5-12 12 0 8 12 20 12 20s12-12 12-20c0-7-5-12-12-12z"/>
      <path d="M611 273c-7 0-12 5-12 12 0 8 12 20 12 20s12-12 12-20c0-7-5-12-12-12z"/>
      <path d="M840 146c-7 0-12 5-12 12 0 8 12 20 12 20s12-12 12-20c0-7-5-12-12-12z"/>
      <path d="M995 388c-7 0-12 5-12 12 0 8 12 20 12 20s12-12 12-20c0-7-5-12-12-12z"/>
    </g>
  </svg>
</section>

<section class="contact">
  <div class="abs cimg" role="img" aria-label="Laser nozzle cutting an ornate pattern in metal"></div>
  <form class="abs contact-form">
    <h2 class="heading">Get In Touch With <span>Us</span></h2>
    <div class="row"><div class="field">First name <svg width="14" height="14" viewBox="0 0 14 14"><circle cx="7" cy="4.5" r="3" fill="none" stroke="var(--red)"/><path d="M1.5 13c0-3 2.5-5 5.5-5s5.5 2 5.5 5z" fill="none" stroke="var(--red)"/></svg></div><div class="field">Last name <svg width="14" height="14" viewBox="0 0 14 14"><circle cx="7" cy="4.5" r="3" fill="none" stroke="var(--red)"/><path d="M1.5 13c0-3 2.5-5 5.5-5s5.5 2 5.5 5z" fill="none" stroke="var(--red)"/></svg></div></div>
    <div class="row"><div class="field">Email <svg width="15" height="12" viewBox="0 0 15 12"><rect x="1" y="1" width="13" height="10" fill="none" stroke="var(--red)"/><path d="M1 1l6.5 5L14 1" fill="none" stroke="var(--red)"/></svg></div><div class="field">Company <svg width="14" height="14" viewBox="0 0 14 14"><rect x="1" y="2" width="7" height="11" fill="none" stroke="var(--red)"/><rect x="8" y="6" width="5" height="7" fill="none" stroke="var(--red)"/></svg></div></div>
    <div class="row"><div class="field">Inquiry <svg width="12" height="8" viewBox="0 0 12 8"><path d="M1 1l5 5 5-5" fill="none" stroke="#222" stroke-width="1.6"/></svg></div></div>
    <div class="row"><div class="field msg">Message <svg width="14" height="14" viewBox="0 0 14 14"><circle cx="7" cy="7" r="6" fill="none" stroke="var(--red)"/><circle cx="4.5" cy="7" r=".8" fill="var(--red)"/><circle cx="7" cy="7" r=".8" fill="var(--red)"/><circle cx="9.5" cy="7" r=".8" fill="var(--red)"/></svg></div></div>
    <span class="btn">Submit</span>
  </form>
</section>

<footer class="site-footer">
  <div class="abs foot-brand">BROVIMARK<small>CALL 555-014-2210</small></div>
  <div class="abs col" style="left:539px"><h4>Quick Links</h4><ul><li>Home</li><li>About Us</li><li>Products</li><li>Solutions</li><li>Industries</li><li>Services</li></ul></div>
  <div class="abs col" style="left:734px"><h4>Resources</h4><ul><li>Privacy Policy</li><li>Terms Of Service</li><li>Contact</li></ul></div>
  <div class="abs col" style="left:920px"><h4>Contact Info</h4><ul>
    <li class="ic"><svg width="14" height="16" viewBox="0 0 14 16"><path d="M7 1a5 5 0 0 0-5 5c0 4 5 9 5 9s5-5 5-9a5 5 0 0 0-5-5z" fill="var(--blue)"/><circle cx="7" cy="6" r="2" fill="#232323"/></svg>Westfield, IL 60000</li>
    <li class="ic"><svg width="15" height="12" viewBox="0 0 15 12"><rect width="15" height="12" rx="1" fill="var(--blue)"/><path d="M1 1l6.5 5L14 1" fill="none" stroke="#232323"/></svg>info@brovimark.com</li>
    <li class="ic"><svg width="14" height="14" viewBox="0 0 14 14"><path d="M3 1l3 3-2 2c1 2 2 3 4 4l2-2 3 3-2 2C6 13 1 8 1 3z" fill="var(--blue)"/></svg>555-014-2210</li>
  </ul></div>
  <div class="abs foot-rule"></div>
  <div class="abs copyright">Copyright © 2024 BROVIMARK, LLC. All Rights Reserved.</div>
  <div class="abs social"><span></span><span></span><span></span><span></span></div>
</footer>

</body>
</html>
```